Tech business card design

We need an amazing business card design for our new business 'Pexla' a marketing tech startup based in Sydney, Australia. We provide an online marketplace for businesses to search and buy advertising media, connect with service providers and learn more about marketing. We wish to communicate 'cool tech', reliability and professionalism and design based around our logo.

Target Market(s)

Business Owners

Contact Information for Business Card

Name
Position
Email Address
Website
Phone Number

Font styles to use
Other font styles liked:
• Avenir & Avenir Next

Colors

Designer to choose colors to be used in the design.

```html
<!DOCTYPE html>
<html lang="en">
<head>
<meta charset="utf-8">
<title>Pexla Business Card</title>
<link rel="stylesheet" href="https://fonts.googleapis.com/css2?family=Work+Sans:wght@400;500;700&display=swap">
<style>
  :root {
    --backdrop: #161616;
    --card: #262626;
    --card-edge: #2e2e2e;
    --ink: #f4f4f6;
    --ink-soft: #e2e2e6;
    --emboss: #4a4a4c;
    --rule: #d9d9dc;
  }
  * { margin: 0; padding: 0; box-sizing: border-box; }
  html, body {
    width: 1200px;
    height: 900px;
    overflow: hidden;
    background: var(--backdrop);
    font-family: "Work Sans", "Helvetica Neue", Arial, sans-serif;
  }
  .stage {
    width: 1200px;
    height: 900px;
    display: flex;
    flex-direction: column;
    align-items: center;
    justify-content: center;
    gap: 40px;
  }
  .card {
    width: 630px;
    height: 360px;
    background: var(--card);
    border: 1px solid var(--card-edge);
    box-shadow: 0 12px 30px rgba(0, 0, 0, 0.55);
    position: relative;
  }
  .card--front {
    display: flex;
    align-items: center;
    justify-content: center;
  }
  .wordmark {
    font-weight: 700;
    letter-spacing: -0.02em;
    line-height: 1;
  }
  .card--front .wordmark {
    font-size: 104px;
    color: var(--emboss);
  }
  .card--back {
    display: flex;
    align-items: center;
    padding: 0 48px 0 56px;
  }
  .card--back .wordmark {
    font-size: 96px;
    color: var(--ink);
    width: 290px;
  }
  .divider {
    width: 1px;
    height: 170px;
    background: var(--rule);
    margin: 0 36px 0 10px;
  }
  .contact { color: var(--ink); }
  .contact__name {
    font-size: 25px;
    font-weight: 500;
    line-height: 1.1;
  }
  .contact__role {
    font-size: 16px;
    font-weight: 400;
    color: var(--ink-soft);
    margin-bottom: 18px;
  }
  .contact__address {
    font-size: 17px;
    line-height: 1.3;
    margin-bottom: 14px;
    font-style: normal;
  }
  .contact__list { list-style: none; }
  .contact__item {
    display: flex;
    align-items: center;
    gap: 12px;
    font-size: 17px;
    line-height: 1.5;
  }
  .contact__icon {
    width: 12px;
    height: 12px;
    flex: none;
    stroke: var(--ink);
    fill: none;
    stroke-width: 1.4;
  }
</style>
</head>
<body>
<main class="stage">
  <section class="card card--front" aria-label="Card front">
    <span class="wordmark">Pexla</span>
  </section>

  <section class="card card--back" aria-label="Card back">
    <span class="wordmark">Pexla</span>
    <span class="divider"></span>
    <div class="contact">
      <p class="contact__name">Daniel Harper</p>
      <p class="contact__role">Director</p>
      <address class="contact__address">218 Larkin Avenue<br>Dayton, OH 45402</address>
      <ul class="contact__list">
        <li class="contact__item">
          <svg class="contact__icon" viewBox="0 0 12 12" aria-hidden="true"><path d="M2.5 1 L4.5 1 L5 3.5 L3.8 4.4 Q5 7 7.6 8.2 L8.5 7 L11 7.5 L11 9.5 Q10.5 11 9 11 Q2 10 1 3 Q1 1.5 2.5 1 Z"/></svg>
          <span>+330 5812-3094</span>
        </li>
        <li class="contact__item">
          <svg class="contact__icon" viewBox="0 0 12 12" aria-hidden="true"><rect x="1" y="2.5" width="10" height="7"/><path d="M1 2.5 L6 6.5 L11 2.5"/></svg>
          <span>info@pexla.com</span>
        </li>
        <li class="contact__item">
          <svg class="contact__icon" viewBox="0 0 12 12" aria-hidden="true"><circle cx="6" cy="6" r="5"/><ellipse cx="6" cy="6" rx="2.2" ry="5"/><path d="M1 6 H11"/></svg>
          <span>www.pexla.com</span>
        </li>
      </ul>
    </div>
  </section>
</main>
</body>
</html>
```